Professional Package for CPA Firm

We would like a stationery design for our new CPA Firm based in Atlanta, GA called 'Vale 8'. We work with investors to help grow investments, tax free. We would like the design to have a professional/minimal look with a 'wow' factor. We need 9.5″ x 4.125″, 9x12, and 10x13 mailing envelopes, business cards, and a letterhead. We have a logo that is already complete. For the letterhead, we would like to have space to put credentials at the bottom of the page

Industry/Entity Type

CPA, Accounting

```html
<!DOCTYPE html>
<html lang="en">
<head>
<meta charset="utf-8">
<title>Vale 8 — Business Cards</title>
<link rel="stylesheet" href="https://fonts.googleapis.com/css2?family=Open+Sans:wght@400;600;700&display=swap">
<style>
  :root {
    --backdrop: #2a2c2f;
    --card: #0d3552;
    --teal: #2bb7c4;
    --coral: #f2575a;
    --white: #ffffff;
    --muted: #b9c6d2;
  }
  * { box-sizing: border-box; margin: 0; padding: 0; }
  html, body {
    width: 1200px; height: 874px; overflow: hidden;
    background: var(--backdrop);
    font-family: "Open Sans", Arial, sans-serif;
  }
  .canvas { position: relative; width: 1200px; height: 874px; }
  .card {
    position: absolute;
    width: 580px; height: 330px;
    background: var(--card);
    border-radius: 18px;
    box-shadow: 0 10px 28px rgba(0,0,0,.45);
  }
  .card--front { left: 420px; top: 62px; }
  .card--back { left: 200px; top: 478px; }

  .brand { display: flex; flex-direction: column; }
  .brand__row { display: flex; align-items: center; gap: 14px; }
  .brand__mark { width: 26px; height: 26px; background: var(--coral); }
  .brand__name {
    font-weight: 700; color: var(--white); letter-spacing: 3px; line-height: 1;
  }
  .brand__tagline { color: var(--white); letter-spacing: 2px; }

  .card--front .brand {
    position: absolute; left: 0; right: 0; top: 118px; align-items: center;
  }
  .card--front .brand__name { font-size: 58px; }
  .card--front .brand__tagline { font-size: 15px; margin-top: 10px; color: var(--muted); }

  .card--back .brand {
    position: absolute; left: 40px; top: 128px; width: 230px;
  }
  .card--back .brand__name { font-size: 48px; }
  .card--back .brand__tagline { font-size: 13px; margin-top: 8px; }

  .divider {
    position: absolute; left: 292px; top: 60px; width: 2px; height: 210px;
    background: var(--teal);
  }
  .contact { position: absolute; left: 318px; top: 58px; color: var(--white); }
  .contact__name { font-size: 21px; font-weight: 600; color: var(--teal); letter-spacing: .5px; line-height: 1.1; }
  .contact__role { font-size: 15px; color: var(--coral); margin-bottom: 14px; }
  .contact__address { font-size: 15px; line-height: 1.35; margin-bottom: 12px; }
  .contact__list { list-style: none; font-size: 15px; line-height: 1.4; }
  .contact__list li { display: flex; align-items: center; gap: 10px; }
  .contact__list svg { width: 13px; height: 13px; fill: var(--coral); flex: none; }
</style>
</head>
<body>
<main class="canvas">
  <section class="card card--front" aria-label="Business card front">
    <div class="brand">
      <div class="brand__row">
        <span class="brand__mark"></span>
        <span class="brand__name">VALE 8</span>
      </div>
      <span class="brand__tagline">CPAs and Tax Advisors</span>
    </div>
  </section>

  <section class="card card--back" aria-label="Business card back">
    <div class="brand">
      <div class="brand__row">
        <span class="brand__mark"></span>
        <span class="brand__name">VALE 8</span>
      </div>
      <span class="brand__tagline">CPAs and Tax Advisors</span>
    </div>
    <div class="divider"></div>
    <div class="contact">
      <p class="contact__name">DANIEL HART</p>
      <p class="contact__role">President</p>
      <p class="contact__address">412 Birchwood Lane<br>Juneau, Alaska 99801</p>
      <ul class="contact__list">
        <li><svg viewBox="0 0 16 16" aria-hidden="true"><path d="M3.6 1.2l2.3 2.6-1.3 2a9 9 0 0 0 5.6 5.6l2-1.3 2.6 2.3-1.6 2.4C7.4 14.4 1.6 8.6 1.2 2.8z"/></svg>555-214-7730</li>
        <li><svg viewBox="0 0 16 16" aria-hidden="true"><path d="M4 0h8a1 1 0 0 1 1 1v14a1 1 0 0 1-1 1H4a1 1 0 0 1-1-1V1a1 1 0 0 1 1-1zm1 2v10h6V2zm3 11a1 1 0 1 0 0 2 1 1 0 0 0 0-2z"/></svg>555-381-6042</li>
        <li><svg viewBox="0 0 16 16" aria-hidden="true"><path d="M0 3h16v10H0zm1.5 1.2L8 9l6.5-4.8V4h-13z"/></svg>info@vale8.com</li>
        <li><svg viewBox="0 0 16 16" aria-hidden="true"><path d="M8 0a8 8 0 1 0 0 16A8 8 0 0 0 8 0zm0 1.5c.9 0 2 2 2.2 5.5H5.8C6 3.5 7.1 1.5 8 1.5zM1.6 8.5h2.7c.1 2 .5 3.8 1.2 5A6.5 6.5 0 0 1 1.6 8.5zm0-1.5A6.5 6.5 0 0 1 5.5 2.5c-.7 1.2-1.1 3-1.2 4.5zm4.2 1.5h4.4C10 12 8.9 14.5 8 14.5S6 12 5.8 8.5zm5.9 0h2.7a6.5 6.5 0 0 1-3.9 5c.7-1.2 1.1-3 1.2-5zm0-1.5c-.1-1.5-.5-3.3-1.2-4.5A6.5 6.5 0 0 1 14.4 7z"/></svg>www.vale8.com</li>
      </ul>
    </div>
  </section>
</main>
</body>
</html>
```